Brightwell Practice Partners, Inc (www.brightwellpracticepartnrs.example) would like to design a website to convey a level of professionalism to healthcare providers that we are the place form them to visit for Contin. Education, Marketing and Management, Joint Venture Partnerships, etc.
We think we would like a WP Site so that we can use the dynamic and static sides of it's capabilities. We also want to have something that acts as a membership side where members can post their Bio and CV's and prospective employers can post help wanted ads.

Target Market(s)

Pediatricians, Pediatric Dentist, Employers seeking these doctors

Industry/Entity Type

Healthcare

Requirements
Must have
• Services:
Resumes/Bio
Help Wanted
Continuing Education Programs
Marketing & Management

```html
<!DOCTYPE html>
<html lang="en">
<head>
<meta charset="utf-8">
<title>Brightwell Practice Partners, Inc</title>
<link rel="stylesheet" href="https://fonts.googleapis.com/css2?family=Dosis:wght@400;500&family=Ubuntu:ital,wght@0,300;0,400;0,500;0,700;1,300;1,400&display=swap">
<style>
:root{
  --navy:#1f2c4e;
  --navy-2:#2c3d68;
  --sky:#4aa9e8;
  --sky-light:#8fd0f5;
  --bar:#3d9be0;
  --bar-line:#6bb9ee;
  --yellow:#f7d417;
  --orange:#f39c12;
  --link:#1f93dc;
  --text:#555;
  --heading:#2a2a2a;
  --line:#d8d8d8;
  --footer:#eeeeee;
  --white:#fff;
}
*{box-sizing:border-box;margin:0;padding:0}
html,body{width:888px;height:1200px;overflow:hidden;background:var(--white)}
body{position:relative;font-family:"Ubuntu",sans-serif;color:var(--text)}
.abs{position:absolute}

.topbar{left:0;top:0;width:888px;height:29px;background:#1b2645;font-size:9.5px;color:#c7cfe2;text-align:right;padding:9px 50px 0 0}
.topbar span{margin:0 4px}
.header{left:0;top:29px;width:888px;height:91px;background:linear-gradient(#2b3b64,#24335a)}
.brand{left:38px;top:30px;font-family:"Ubuntu",sans-serif;font-weight:500;font-size:26px;color:var(--white);letter-spacing:.5px}
.nav{left:364px;top:47px;display:flex;align-items:center;font-size:12.5px;color:var(--white)}
.nav a{color:var(--white);text-decoration:none;padding:6px 17px;border-radius:14px}
.nav a.active{background:#16213d}
.nav .sep{color:#c7cfe2}

.hero{left:0;top:120px;width:888px;height:260px;background:radial-gradient(circle at 620px 120px,#b9e5fb 0,#73c3f1 30%,#4aa9e8 70%)}
.hero-box{left:29px;top:30px;width:425px;height:188px;border-radius:8px;background:rgba(120,190,240,.55)}
.hero-box h1{position:absolute;left:25px;top:20px;font-family:"Dosis",sans-serif;font-weight:400;font-size:34px;color:var(--white)}
.hero-box p{position:absolute;left:25px;top:72px;width:385px;font-size:10px;line-height:15.5px;color:var(--white)}
.upload{position:absolute;left:24px;top:128px;width:345px;height:30px;background:var(--white);border-radius:4px;font-size:11.5px;color:#888;padding:9px 12px}
.browse{position:absolute;left:263px;top:125px;width:101px;height:35px;background:var(--yellow);border-radius:8px;font-family:"Dosis",sans-serif;font-size:15px;color:#3a3200;text-align:center;line-height:35px}
.portrait{left:537px;top:6px;width:269px;height:254px;border-radius:120px 120px 0 0;background:linear-gradient(#7a4b34,#e7b596 45%,#f3f3f3 85%)}

.actionbar{left:0;top:380px;width:888px;height:54px;background:linear-gradient(#4aa9e8,#3a97dc);border-bottom:3px solid #7cc4f1;display:flex}
.action{height:51px;display:flex;align-items:center;gap:8px;font-family:"Dosis",sans-serif;font-size:18px;color:var(--white);border-right:1px solid var(--bar-line)}
.action:last-child{border-right:0}

.card{top:457px;height:136px;border:1px solid var(--line);border-radius:3px;padding:13px 18px;background:var(--white);box-shadow:0 1px 2px rgba(0,0,0,.08)}
.card h2{font-family:"Dosis",sans-serif;font-weight:400;font-size:18px;color:var(--link)}
.card p{margin-top:6px;font-size:9.5px;line-height:14.8px;color:#666;font-weight:300}
.more{display:flex;align-items:center;gap:5px;margin-top:10px;font-family:"Dosis",sans-serif;font-size:13.5px;color:var(--link)}

.panel{top:603px;height:515px;border:1px solid var(--line);border-radius:4px;background:var(--white)}
.panel h3{font-family:"Dosis",sans-serif;font-weight:400;font-size:18.5px;color:var(--heading)}
.resume{position:absolute;left:22px;width:520px;height:100px}
.avatar{position:absolute;left:0;top:0;width:85px;height:72px;border:1px solid var(--line);border-radius:3px;background:linear-gradient(#fff 0,#f1f1f1 40%,#4a9ee0 80%)}
.resume .name{position:absolute;left:109px;top:0;font-family:"Ubuntu",sans-serif;font-size:12px;color:#222}
.resume .desc{position:absolute;left:109px;top:19px;width:410px;font-size:9.5px;line-height:13px;color:#666;font-weight:300}
.resume .meta{position:absolute;left:110px;top:50px;font-size:9.5px;color:var(--orange)}
.resume .btn{position:absolute;left:108px;top:69px;padding:4px 11px;background:var(--orange);border-radius:3px;color:var(--white);font-size:9.5px}

.story{font-style:italic;font-weight:300;font-size:9.3px;line-height:14.8px;color:#555}
.rule{position:absolute;left:14px;width:272px;height:1px;background:var(--line)}
.side-h{position:absolute;left:16px;display:flex;align-items:center;gap:7px;font-family:"Dosis",sans-serif;font-size:18.5px;color:var(--heading)}
.side-p{position:absolute;left:18px;width:270px;font-style:italic;font-weight:300;font-size:9.3px;line-height:14.6px;color:#555;text-align:justify}
.rm{position:absolute;right:18px;font-family:Georgia,serif;font-size:11px;color:#111}

.footer{left:0;top:1118px;width:888px;height:82px;background:var(--footer);font-size:9.8px;color:#555}
.footer .links{position:absolute;left:19px;top:20px;word-spacing:2px}
.footer .links span{margin:0 8px;color:#888}
.footer .copy{position:absolute;left:19px;top:46px}
</style>
</head>
<body>

<div class="abs topbar">Member Login <span>|</span> Faq's <span>|</span> Sign Up <span>|</span> Support</div>
<header class="abs header">
  <div class="abs brand">BPP</div>
  <nav class="abs nav">
    <a class="active">Main</a><a>About Us</a><span class="sep">|</span><a>Get Job</a><span class="sep">|</span><a>Post Now</a><span class="sep">|</span><a>Update</a><span class="sep">|</span><a>Contact</a>
  </nav>
</header>

<section class="abs hero">
  <div class="abs portrait" role="img" aria-label="Photo of a smiling professional woman"></div>
  <div class="abs hero-box">
    <h1>Post your Resume Now</h1>
    <p>We at Northlake Studio provide you the best simple websites too with total work done as using all the best designing and all done so that you can achieve the goal of yours through our work done on your website.</p>
    <div class="upload">Browse your resume</div>
    <div class="browse">Browse Now</div>
  </div>
</section>

<div class="abs actionbar">
  <div class="action" style="width:213px;padding-left:38px">
    <svg width="26" height="26" viewBox="0 0 26 26"><path d="M10 2h6v9h5l-8 8-8-8h5z" fill="#fff"/><path d="M2 18v5h22v-5" stroke="#fff" stroke-width="3" fill="none"/></svg>Post Wanted Ads</div>
  <div class="action" style="width:169px;padding-left:16px">
    <svg width="26" height="26" viewBox="0 0 26 26" fill="none" stroke="#fff" stroke-width="2"><path d="M4 22l2-7 13-13 5 5-13 13z"/><path d="M4 22l7-2"/><path d="M16 5l5 5"/></svg>Get Job Offers</div>
  <div class="action" style="width:222px;padding-left:30px">
    <svg width="22" height="22" viewBox="0 0 22 22"><path d="M8 1h6v7h7v6h-7v7H8v-7H1V8h7z" fill="#fff"/></svg>Create Resume now</div>
  <div class="action" style="width:284px;padding-left:23px">
    <svg width="28" height="28" viewBox="0 0 28 28" fill="none" stroke="#fff" stroke-width="3.5"><path d="M5 12a9 9 0 0 1 16-4"/><path d="M23 16a9 9 0 0 1-16 4"/><path d="M17 3l5 5-6 1" fill="#fff" stroke-width="1"/><path d="M11 25l-5-5 6-1" fill="#fff" stroke-width="1"/></svg>Check Latest Updates</div>
</div>

<article class="abs card" style="left:16px;width:275px">
  <h2>Job Postings</h2>
  <p>Northlake Studio is specialized in handling advanced web projects and the ongoing projects that require permanent maintenance and support .We like challenges and do complete</p>
  <div class="more"><svg width="13" height="13" viewBox="0 0 13 13"><path d="M1 4h6V0l6 6.5L7 13V9H1z" fill="#2b9ae0"/></svg>read more</div>
</article>
<article class="abs card" style="left:303px;width:276px">
  <h2>Check Profile</h2>
  <p>Northlake Studio is specialized in handling advanced web projects and the ongoing projects that require permanent maintenance and support .We like challenges and do complete</p>
  <div class="more"><svg width="13" height="13" viewBox="0 0 13 13"><path d="M1 4h6V0l6 6.5L7 13V9H1z" fill="#2b9ae0"/></svg>read more</div>
</article>
<article class="abs card" style="left:590px;width:277px">
  <h2>Sign Up Form</h2>
  <p>Northlake Studio is specialized in handling advanced web projects and the ongoing projects that require permanent maintenance and support .We like challenges and do complete</p>
  <div class="more"><svg width="13" height="13" viewBox="0 0 13 13"><path d="M1 4h6V0l6 6.5L7 13V9H1z" fill="#2b9ae0"/></svg>read more</div>
</article>

<section class="abs panel" style="left:16px;width:558px">
  <h3 class="abs" style="left:24px;top:10px">Latest Resume Updates</h3>
  <div class="resume" style="top:52px"><div class="avatar" role="img" aria-label="Candidate avatar illustration"></div><div class="name">Candidate Name here</div><div class="desc">We like challenges and do complete these challenge with expertise we like solving questions that arises in such projects as these helps us to grow also.</div><div class="meta">MBBS, PHD In 2005 &nbsp;|&nbsp; 5 Year Experience</div><div class="btn">full details</div></div>
  <div class="resume" style="top:166px"><div class="avatar" role="img" aria-label="Candidate avatar illustration"></div><div class="name">Candidate Name here</div><div class="desc">We like challenges and do complete these challenge with expertise we like solving questions that arises in such projects as these helps us to grow also.</div><div class="meta">MBBS, PHD in 2005 &nbsp;|&nbsp; 5 Year Experience</div><div class="btn">full details</div></div>
  <div class="resume" style="top:278px"><div class="avatar" role="img" aria-label="Candidate avatar illustration"></div><div class="name">Candidate Name here</div><div class="desc">We like challenges and do complete these challenge with expertise we like solving questions that arises in such projects as these helps us to grow also.</div><div class="meta">MBBS, PHD in 2005 &nbsp;|&nbsp; 5 Year Experience</div><div class="btn">full details</div></div>
  <div class="resume" style="top:395px"><div class="avatar" role="img" aria-label="Candidate avatar illustration"></div><div class="name">Candidate Name here</div><div class="desc">We like challenges and do complete these challenge with expertise we like solving questions that arises in such projects as these helps us to grow also.</div><div class="meta">MBBS, PHD in 2005 &nbsp;|&nbsp; 5 Year Experience</div><div class="btn">full details</div></div>
</section>

<aside class="abs panel" style="left:578px;width:299px">
  <h3 class="abs" style="left:19px;top:10px">Sucess Stories</h3>
  <div class="abs" role="img" aria-label="Portrait photo of a member" style="left:13px;top:48px;width:77px;height:68px;border:1px solid var(--line);border-radius:3px;background:linear-gradient(#f4f4f4,#c9a58c 50%,#9aa3ae)"></div>
  <p class="abs story" style="left:109px;top:52px;width:180px"><span style="font-size:14px;color:#aaa">&ldquo;</span> BPP is the perfect solution job seekers are looking for, provided you have content with special language (for objective, goals section etc.) ready beforehand. If you don't, you might want to sit down first and think through exactly what you want from a resume. <span style="font-size:14px;color:#aaa">&rdquo;</span></p>
  <div class="abs" style="right:19px;top:160px;font-family:Georgia,serif;font-size:11px;color:#111">by Author Name</div>
  <div class="rule" style="top:188px"></div>
  <div class="side-h" style="top:203px"><svg width="30" height="16" viewBox="0 0 30 16" fill="none" stroke="#2b6ca8" stroke-width="1.3"><path d="M2 12L9 3l6 3 6-3 7 9-13 3z"/><path d="M15 6v9"/></svg>Continuing Education</div>
  <p class="side-p" style="top:235px">Lorem Ipsum is simply dummy text of the printing and typesetting industry. Lorem Ipsum has been the industry's standard dummy text ever since the 1500s.</p>
  <p class="side-p" style="top:282px">when an unknown printer took a galley of type and scrambled it to make a type specimen book</p>
  <div class="rm" style="top:322px">Read more &gt;&gt;</div>
  <div class="rule" style="top:343px"></div>
  <div class="side-h" style="top:355px"><svg width="14" height="30" viewBox="0 0 14 30"><circle cx="7" cy="4" r="3.5" fill="#2a3a5c"/><path d="M2 10h10v11H9v8H5v-8H2z" fill="#2a3a5c"/></svg>Managment &amp; Marketing</div>
  <p class="side-p" style="top:387px">Lorem Ipsum is simply dummy text of the printing and typesetting industry. Lorem Ipsum has been the industry's standard dummy text ever since the 1500s.</p>
  <p class="side-p" style="top:434px">when an unknown printer took a galley of type and scrambled it to make a type specimen book</p>
  <div class="rm" style="top:480px">Read more &gt;&gt;</div>
</aside>

<footer class="abs footer">
  <div class="links">Main<span>|</span>About Us<span>|</span>Get Job<span>|</span>Post Now<span>|</span>Update<span>|</span>Contact</div>
  <div class="copy">&copy; 2012 Company Name &nbsp;|&nbsp; All right reserved</div>
</footer>

</body>
</html>
```